Baby Boutique Needs a Business Card Design

We need a modern double sided business card design using the attached logo for Little Wren Nook.

Little Wren Nook is a baby boutique which sells only handmade clothing and accessories for both boys and girls. Our store will live exclusively online.

We would like to only use the colors that have been used in the logo.

Target Market(s)

Potential wholesale clients, Small business owners

Industry/Entity Type

Retail

Contact Information for Business Card

Name Gideon R. Falkner (Owner)
Email sales@littlewrennook.example
Main Phone 555-203-7719
Cell phone 555-203-7746
Website www.LittleWrenNook.example

Font styles to use
Sans Serif

Colors

Designer to choose colors to be used in the design.

Requirements
Must have
• -Would like to have icons that indentify the contact information.
• -Include our website
• -Include our tagline in a small area near the bottom. "Handmade Baby Creations"
• -Would like to include Facebook and Instagram Icons
• -
Nice to have
• Would like to have a simple back side with the logo.
• Something along the lines of the meadowfield lending card attached.

```html
<!DOCTYPE html>
<html lang="en">
<head>
<meta charset="utf-8">
<title>Little Wren Nook — Business Card</title>
<link rel="stylesheet" href="https://fonts.googleapis.com/css2?family=Arimo:wght@400;700&display=swap">
<style>
  :root {
    --backdrop: #2a2a2c;
    --card: #1b1b1d;
    --teal: #74cbbc;
    --coral: #e35d5f;
    --ink: #1b1b1d;
  }
  * { box-sizing: border-box; margin: 0; padding: 0; }
  html, body {
    width: 1200px; height: 1189px; overflow: hidden;
    background: var(--backdrop);
    font-family: "Arimo", Arial, sans-serif;
  }
  .card {
    position: absolute; left: 150px;
    width: 900px; height: 514px;
    background: var(--card);
    border-radius: 34px;
    overflow: hidden;
    box-shadow: 0 18px 40px rgba(0,0,0,.45);
  }
  .card--back { top: 40px; }
  .card--front { top: 635px; }

  /* Brand lockup */
  .brand {
    position: absolute;
    display: flex; align-items: center; gap: 14px;
  }
  .brand__name {
    color: var(--teal);
    font-weight: 700;
    line-height: 1.02;
  }
  .brand__emblem {
    background: var(--coral);
    border-radius: 50% 50% 50% 50% / 60% 60% 40% 40%;
    opacity: .85;
  }

  /* Back side */
  .card--back .brand { left: 290px; top: 150px; }
  .card--back .brand__name { font-size: 54px; }
  .card--back .brand__emblem { width: 80px; height: 90px; }
  .faint-motif {
    position: absolute; left: 40px; top: 250px;
    width: 300px; height: 230px;
    border-radius: 45%;
    background: radial-gradient(ellipse at center, rgba(227,93,95,.10), rgba(227,93,95,0) 70%);
  }
  .social {
    position: absolute; left: 405px; top: 320px;
    display: flex; gap: 12px;
  }
  .social__tile {
    width: 40px; height: 40px; border-radius: 4px;
    background: var(--teal);
  }
  .web-line {
    position: absolute; left: 0; right: 0; top: 388px;
    text-align: center;
    color: var(--teal);
    font-size: 20px; letter-spacing: 4px;
  }

  /* Front side */
  .card--front .brand { left: 60px; top: 150px; width: 380px; }
  .card--front .brand__name { font-size: 48px; }
  .card--front .brand__emblem { flex: none; width: 70px; height: 80px; }
  .divider {
    position: absolute; left: 480px; top: 70px;
    width: 2px; height: 200px; background: var(--teal);
  }
  .contact { position: absolute; left: 515px; top: 80px; }
  .contact__name { color: var(--teal); font-weight: 700; font-size: 27px; }
  .contact__role { color: var(--coral); font-size: 20px; margin-bottom: 12px; }
  .contact__list { list-style: none; }
  .contact__item {
    display: flex; align-items: center; gap: 12px;
    color: var(--teal); font-size: 19px; line-height: 27px;
  }
  .contact__item svg { width: 18px; height: 18px; flex: none; }
  .band-rule {
    position: absolute; left: 0; right: 0; top: 374px;
    height: 4px; background: var(--coral);
  }
  .tagline-band {
    position: absolute; left: 0; right: 0; top: 392px; bottom: 0;
    background: var(--teal);
    display: flex; align-items: flex-start; justify-content: center;
    padding-top: 18px;
  }
  .tagline {
    color: var(--ink); font-size: 22px; letter-spacing: 7px;
  }
</style>
</head>
<body>

<section class="card card--back" aria-label="Card back">
  <div class="faint-motif" role="img" aria-label="Faint stork carrying a bundle, large background decoration"></div>
  <div class="brand">
    <span class="brand__name">Little Wren<br>Nook</span>
    <span class="brand__emblem" role="img" aria-label="Stork carrying a baby bundle illustration"></span>
  </div>
  <div class="social">
    <span class="social__tile" aria-label="Social profile"></span>
    <span class="social__tile" aria-label="Social profile"></span>
  </div>
  <p class="web-line">www.LittleWrenNook.example</p>
</section>

<section class="card card--front" aria-label="Card front">
  <div class="brand">
    <span class="brand__name">Little Wren<br>Nook</span>
    <span class="brand__emblem" role="img" aria-label="Stork carrying a baby bundle illustration"></span>
  </div>
  <div class="divider"></div>
  <div class="contact">
    <p class="contact__name">Gideon R. Falkner</p>
    <p class="contact__role">Owner</p>
    <ul class="contact__list">
      <li class="contact__item">
        <svg viewBox="0 0 20 20" aria-hidden="true"><path fill="var(--coral)" d="M2 7c0-3 4-5 8-5s8 2 8 5l-4 1-1-2H7L6 8z M5 9h10l2 8H3z"/></svg>
        555-203-7719
      </li>
      <li class="contact__item">
        <svg viewBox="0 0 20 20" aria-hidden="true"><rect x="5" y="1.5" width="10" height="17" rx="2" fill="none" stroke="var(--coral)" stroke-width="2"/><circle cx="10" cy="15" r="1.2" fill="var(--coral)"/></svg>
        555-203-7746
      </li>
      <li class="contact__item">
        <svg viewBox="0 0 20 20" aria-hidden="true"><rect x="1" y="4" width="18" height="12" fill="var(--coral)"/><path d="M1 4l9 7 9-7" fill="none" stroke="var(--card)" stroke-width="1.5"/></svg>
        sales@littlewrennook.example
      </li>
      <li class="contact__item">
        <svg viewBox="0 0 20 20" aria-hidden="true"><g fill="none" stroke="var(--coral)" stroke-width="1.5"><circle cx="10" cy="10" r="8"/><ellipse cx="10" cy="10" rx="3.5" ry="8"/><path d="M2 10h16M3.5 6h13M3.5 14h13"/></g></svg>
        www.LittleWrenNook.example
      </li>
    </ul>
  </div>
  <div class="band-rule"></div>
  <div class="tagline-band">
    <p class="tagline">Handmade Baby Creations</p>
  </div>
</section>

</body>
</html>
```